Thornvale Group needs a business card design

We need a new business card design using the logo recently selected in a logo competition on Pixel Bazaar. Our business is a consultancy specializing in aviation and energy and the winning business card design will promote an image of precision and professionalism with creativity.

Please use the logo with the name on the front of the card and use a complementary font. Make the back white with either the light grey or dark grey logo.

Target Market(s)

Senior finance and legal leaders at aviation and energy companies

Industry/Entity Type

Management Consulting

Contact Information for Business Card

Peter Castrell
President
Thornvale Group

www.thornvalegroup.example

(555) 204-6391
pc@thornvalegroup.example

Requirements
Must have
• Professional font that goes well with the logo font

```html
<!DOCTYPE html>
<html lang="en">
<head>
<meta charset="utf-8">
<title>Thornvale Group – Business Card</title>
<link rel="stylesheet" href="https://fonts.googleapis.com/css2?family=Open+Sans:wght@400;600;700&display=swap">
<style>
  :root {
    --navy: #12406f;
    --charcoal: #666769;
    --ink: #2b2b2b;
    --card: #ffffff;
    --backdrop: #e9e8e5;
    --card-shadow: 0 10px 28px rgba(0, 0, 0, 0.16);
  }
  * { box-sizing: border-box; margin: 0; padding: 0; }
  html, body {
    width: 1200px;
    height: 900px;
    overflow: hidden;
  }
  body {
    background: var(--backdrop);
    font-family: "Open Sans", Arial, sans-serif;
    position: relative;
  }
  .card {
    position: absolute;
    width: 525px;
    height: 300px;
    background: var(--card);
    box-shadow: var(--card-shadow);
  }

  /* Back of card */
  .card-back {
    left: 90px;
    top: 130px;
    display: flex;
    align-items: center;
    justify-content: center;
  }
  .back-name {
    color: var(--charcoal);
    font-weight: 400;
    font-size: 34px;
    letter-spacing: 0.14em;
    text-transform: uppercase;
  }

  /* Front of card */
  .card-front {
    left: 585px;
    top: 470px;
  }
  .contact {
    position: absolute;
    left: 300px;
    top: 34px;
  }
  .contact-name {
    color: var(--navy);
    font-weight: 700;
    font-size: 18px;
    line-height: 1.1;
  }
  .contact-title {
    color: var(--ink);
    font-size: 12.5px;
    margin-left: 4px;
    margin-bottom: 16px;
  }
  .contact-line {
    display: flex;
    align-items: center;
    gap: 8px;
    color: var(--ink);
    font-size: 12.5px;
    line-height: 1.6;
    margin-left: 22px;
  }
  .contact-line svg {
    width: 11px;
    height: 11px;
    fill: var(--navy);
    flex: none;
  }
  .brand {
    position: absolute;
    left: 44px;
    bottom: 44px;
    color: var(--navy);
    font-weight: 400;
    text-transform: uppercase;
    line-height: 1.15;
  }
  .brand-name {
    display: block;
    font-size: 38px;
    letter-spacing: 0.06em;
  }
  .brand-sub {
    display: block;
    font-size: 17px;
    letter-spacing: 0.9em;
    padding-left: 70px;
  }
</style>
</head>
<body>
  <section class="card card-back" aria-label="Card back">
    <span class="back-name">Thornvale Group</span>
  </section>

  <section class="card card-front" aria-label="Card front">
    <div class="contact">
      <p class="contact-name">Peter Castrell</p>
      <p class="contact-title">President</p>
      <p class="contact-line">
        <svg viewBox="0 0 24 24" aria-hidden="true"><path d="M6.6 10.8a15.1 15.1 0 0 0 6.6 6.6l2.2-2.2a1 1 0 0 1 1-.25 11.4 11.4 0 0 0 3.6.57 1 1 0 0 1 1 1V20a1 1 0 0 1-1 1A17 17 0 0 1 3 4a1 1 0 0 1 1-1h3.5a1 1 0 0 1 1 1c0 1.25.2 2.45.57 3.57a1 1 0 0 1-.25 1z"/></svg>
        (555) 204-6391
      </p>
      <p class="contact-line">
        <svg viewBox="0 0 24 24" aria-hidden="true"><path d="M2 5h20v14H2z M3.5 6.5 12 13l8.5-6.5" stroke="#fff" stroke-width="1.5"/></svg>
        pc@thornvalegroup.example
      </p>
    </div>
    <p class="brand">
      <span class="brand-name">Thornvale</span>
      <span class="brand-sub">Group</span>
    </p>
  </section>
</body>
</html>
```